Awesome photographers card for an awesome new business

Double sided business card Black background and silver logo in middle on one side. Details on otherside. please keep it simple

Industry/Entity Type

Photographer

Contact Information for Business Card

Gerald Fenwick
0452817360
GeraldFenwickPhotography47@mailbox.test
www.GeraldFenwickPhotography.test.au
Instagram _Gerald_fenwick

Requirements
Must have
• My logo in Silver
• please use instagram logo instead of "Instagram"

```html
<!DOCTYPE html>
<html lang="en">
<head>
<meta charset="utf-8">
<title>Gerald Fenwick Photography – Business Card</title>
<link href="https://fonts.googleapis.com/css2?family=Open+Sans:wght@400;600&display=swap" rel="stylesheet">
<style>
  :root {
    --page-bg: #e4e2df;
    --card-light: #eceae8;
    --card-mid: #d6d4d1;
    --card-edge: #b9b7b4;
    --band-dark: #3a3938;
    --band-darker: #242323;
    --band-highlight: #9a9897;
    --name-silver: #d9d9d9;
    --ink: #3b3b3b;
    --icon: #444444;
  }
  html, body {
    margin: 0;
    padding: 0;
    width: 1200px;
    height: 969px;
    overflow: hidden;
    background: var(--page-bg);
  }
  .canvas {
    position: relative;
    width: 1200px;
    height: 969px;
  }
  .card {
    position: absolute;
    left: 100px;
    top: 199px;
    width: 1000px;
    height: 571px;
    background: linear-gradient(160deg, var(--card-light) 0%, var(--card-mid) 100%);
    border: 1px solid var(--card-edge);
    box-shadow: 0 12px 30px rgba(0,0,0,0.18);
    overflow: hidden;
    font-family: "Open Sans", sans-serif;
  }
  .card__band {
    position: absolute;
    inset: 0;
    width: 1000px;
    height: 571px;
  }
  .card__title {
    position: absolute;
    right: 52px;
    top: 44px;
    margin: 0;
    font-size: 28px;
    font-weight: 600;
    letter-spacing: 0.5px;
    text-transform: uppercase;
    color: var(--name-silver);
  }
  .brand {
    position: absolute;
    left: 62px;
    top: 210px;
    display: flex;
    align-items: center;
    gap: 16px;
  }
  .brand__dot {
    width: 40px;
    height: 40px;
    border-radius: 50%;
    border: 3px solid var(--ink);
    box-sizing: border-box;
  }
  .brand__name {
    font-size: 30px;
    font-weight: 400;
    color: var(--ink);
  }
  .contact {
    position: absolute;
    left: 62px;
    top: 392px;
    margin: 0;
    padding: 0;
    list-style: none;
  }
  .contact__item {
    display: flex;
    align-items: center;
    height: 32.5px;
    font-size: 24px;
    color: var(--ink);
    white-space: nowrap;
  }
  .contact__icon {
    width: 20px;
    height: 20px;
    margin-right: 18px;
    flex: none;
  }
</style>
</head>
<body>
<div class="canvas">
  <div class="card">
    <svg class="card__band" viewBox="0 0 1000 571" aria-hidden="true">
      <defs>
        <linearGradient id="bandShade" x1="0" y1="0" x2="1" y2="1">
          <stop offset="0" stop-color="var(--band-dark)"/>
          <stop offset="1" stop-color="var(--band-darker)"/>
        </linearGradient>
      </defs>
      <path d="M0,0 H1000 V528 C900,270 640,70 0,42 Z" fill="url(#bandShade)"/>
      <path d="M30,34 C480,44 780,160 930,360" fill="none" stroke="var(--band-highlight)" stroke-width="4" stroke-linecap="round" opacity="0.8"/>
    </svg>

    <h1 class="card__title">Gerald Fenwick</h1>

    <div class="brand">
      <span class="brand__dot"></span>
      <span class="brand__name">Gerald Fenwick</span>
    </div>

    <ul class="contact">
      <li class="contact__item">
        <svg class="contact__icon" viewBox="0 0 20 20" aria-hidden="true">
          <path d="M2,7 C2,4 5,3 10,3 C15,3 18,4 18,7 L14,8 L13,6 H7 L6,8 Z" fill="var(--icon)"/>
          <rect x="4" y="9" width="12" height="8" rx="1.5" fill="var(--icon)"/>
        </svg>
        0452817360
      </li>
      <li class="contact__item">
        <svg class="contact__icon" viewBox="0 0 20 20" aria-hidden="true">
          <rect x="1" y="4" width="18" height="12" fill="var(--icon)"/>
          <path d="M1,4 L10,11 L19,4" fill="none" stroke="#ddd" stroke-width="1.4"/>
        </svg>
        GeraldFenwickPhotography47@mailbox.test
      </li>
      <li class="contact__item">
        <svg class="contact__icon" viewBox="0 0 20 20" aria-hidden="true">
          <circle cx="10" cy="10" r="8.5" fill="var(--icon)"/>
          <path d="M1.5,10 H18.5 M10,1.5 C6,6 6,14 10,18.5 M10,1.5 C14,6 14,14 10,18.5" fill="none" stroke="#ddd" stroke-width="1.2"/>
        </svg>
        www.GeraldFenwickPhotography.test.au
      </li>
      <li class="contact__item">
        <svg class="contact__icon" viewBox="0 0 20 20" aria-hidden="true">
          <rect x="2" y="2" width="16" height="16" fill="var(--icon)"/>
        </svg>
        Gerald_fenwick
      </li>
    </ul>
  </div>
</div>
</body>
</html>
```